Product packaging design for lentils

Looking to create a design for lentils in 4lb format. We are looking to create a base design for the bags, and then from there will have additional designs for the different products with different product name, barcodes and nutritional information.

Industry/Entity Type

Food

```html
<!DOCTYPE html>
<html lang="en">
<head>
<meta charset="utf-8">
<title>Harvestly Lentils Pouch</title>
<link href="https://fonts.googleapis.com/css2?family=Outfit:wght@400;600&family=Mulish:wght@400;700&display=swap" rel="stylesheet">
<style>
  :root {
    --stage: #d2d2d2;
    --pouch: #f4f4f4;
    --pouch-shade: #e6e6e6;
    --green: #7cb342;
    --green-pale: #c5e1a5;
    --ink: #141414;
    --muted: #8a8a8a;
    --lentil-dark: #b4623a;
    --lentil-mid: #c98058;
    --lentil-light: #dfb59c;
  }
  * { margin: 0; padding: 0; box-sizing: border-box; }
  html, body { width: 1200px; height: 800px; overflow: hidden; }
  body { background: var(--stage); position: relative; font-family: "Mulish", sans-serif; }

  .pouch {
    position: absolute; left: 350px; top: 30px; width: 500px; height: 740px;
    background: linear-gradient(90deg, var(--pouch-shade) 0%, var(--pouch) 12%, var(--pouch) 85%, var(--pouch-shade) 100%);
    border-radius: 4px 4px 18px 18px;
    overflow: hidden;
  }
  .dot-pattern {
    position: absolute; left: 69px; top: 0; width: 136px; height: 424px;
    background: linear-gradient(180deg, var(--green) 0%, var(--green-pale) 70%, var(--green) 100%);
    opacity: .55;
  }
  .brand {
    position: absolute; left: 270px; top: 262px; width: 190px;
    display: flex; align-items: center; justify-content: center; gap: 8px;
  }
  .brand-dot { width: 16px; height: 16px; border-radius: 50%; background: var(--green); }
  .brand-name { font-family: "Outfit", sans-serif; font-weight: 600; font-size: 28px; color: var(--green); }
  .product-name {
    position: absolute; left: 288px; top: 318px;
    font-family: "Outfit", sans-serif; font-weight: 600; font-size: 62px; line-height: 1;
    color: var(--ink); letter-spacing: -1px;
    border-bottom: 3px solid var(--green); padding-bottom: 2px;
  }
  .lentil-window {
    position: absolute; left: 0; top: 426px; width: 100%; height: 164px;
    background: linear-gradient(110deg, var(--lentil-light) 0%, var(--lentil-mid) 35%, var(--lentil-dark) 65%, var(--lentil-mid) 100%);
  }
  .description {
    position: absolute; left: 91px; top: 612px; width: 320px;
    font-size: 6.6px; line-height: 1.35; color: var(--muted);
  }
  .claims {
    position: absolute; left: 91px; top: 666px; width: 320px;
    display: flex; align-items: center; justify-content: space-between;
    font-family: "Outfit", sans-serif; font-size: 9.5px; color: #555;
  }
  .claim { display: flex; align-items: center; gap: 3px; }
  .claim svg { width: 16px; height: 16px; }
  .sep { width: 1.5px; height: 5px; background: var(--ink); }
  .net-weight {
    position: absolute; left: 382px; top: 706px;
    font-family: "Outfit", sans-serif; font-weight: 600; font-size: 14px; color: #666;
  }
</style>
</head>
<body>
  <main class="pouch">
    <div class="dot-pattern" role="img" aria-label="Column of green dots fading down the pouch"></div>

    <div class="brand">
      <span class="brand-dot"></span>
      <span class="brand-name">Harvestly</span>
    </div>

    <h1 class="product-name">lentils</h1>

    <div class="lentil-window" role="img" aria-label="Clear window showing red lentils inside the bag"></div>

    <p class="description">Red lentils cook quickly and add gentle earthy flavour to soups, curries, salads and stews. Rinse well, simmer for fifteen minutes until tender, then season to taste. Store sealed in a cool dry place away from light. Naturally rich in plant protein and fibre for everyday meals.</p>

    <ul class="claims">
      <li class="claim">
        <svg viewBox="0 0 16 16"><circle cx="8" cy="8" r="6.5" fill="none" stroke="var(--green)" stroke-width="1.2"/></svg>
        <span>FRESH</span>
      </li>
      <li class="sep"></li>
      <li class="claim">
        <svg viewBox="0 0 16 16"><path d="M8 15V5M8 9L5 6M8 7l3-3" fill="none" stroke="var(--green)" stroke-width="1.2" stroke-linecap="round"/></svg>
        <span>High Fiber</span>
      </li>
      <li class="sep"></li>
      <li class="claim">
        <svg viewBox="0 0 16 16"><path d="M8 1.5C8 1.5 3 8 3 10.5a5 5 0 0 0 10 0C13 8 8 1.5 8 1.5z" fill="none" stroke="var(--green)" stroke-width="1.2"/></svg>
        <span>Low Fat</span>
      </li>
      <li class="sep"></li>
      <li class="claim">
        <svg viewBox="0 0 16 16"><path d="M8 14S1.5 9.8 1.5 5.5A3.2 3.2 0 0 1 8 4a3.2 3.2 0 0 1 6.5 1.5C14.5 9.8 8 14 8 14z" fill="none" stroke="var(--green)" stroke-width="1.2"/><path d="M5.5 7.5l2 2 3-3.5" fill="none" stroke="var(--green)" stroke-width="1.2"/></svg>
        <span>Heart Health</span>
      </li>
    </ul>

    <p class="net-weight">15g</p>
  </main>
</body>
</html>
```